Redesign business cards

We have a new logo and I am not that happy with the layout of our existing card and looking for a change. Font is a bit small and the green can be hard to read. Logo may need a tidy up as the copy I have is not that hi-res too so require you to produce a hi-res version of the logo for us too. There will be three individual business cards to produce with just the names and phone numbers being different. Address will change too, but use what you see on the card for now.

Industry/Entity Type

Business

Requirements
Nice to have
• You could consider a redesign to the new logo, just not too radical. We like the blue and green hexagons as we feel that they are representative of oil industry that we are in.

```html
<!DOCTYPE html>
<html lang="en">
<head>
<meta charset="utf-8">
<title>NovaLube Oil Services – Business Card</title>
<link href="https://fonts.googleapis.com/css2?family=Open+Sans:wght@300;400;600;700&display=swap" rel="stylesheet">
<style>
  :root {
    --bg: #e9e6e1;
    --card-white: #ffffff;
    --brand-green: #8cc63f;
    --brand-blue: #1fa3cf;
    --text-grey: #5a5a5a;
    --divider-grey: #c9c9c9;
    --icon-orange: #f39a1e;
    --shadow: rgba(0,0,0,0.18);
  }
  * { margin: 0; padding: 0; box-sizing: border-box; }
  html, body {
    width: 1200px; height: 829px; overflow: hidden;
    background: var(--bg);
    font-family: "Open Sans", sans-serif;
  }
  .sheet {
    width: 1200px; height: 829px;
    display: flex; align-items: center; justify-content: center; gap: 40px;
  }
  .card {
    position: relative;
    width: 540px; height: 310px;
    border-radius: 2px;
    box-shadow: 0 6px 18px var(--shadow);
    overflow: hidden;
  }

  /* Front */
  .card-front { background: var(--card-white); }
  .brand {
    position: absolute; right: 215px; top: 58px;
    display: flex; flex-direction: column; align-items: flex-end;
  }
  .brand-row { display: flex; align-items: center; gap: 8px; }
  .brand-mark {
    width: 16px; height: 16px; border-radius: 50%;
    background: var(--brand-blue); flex: none;
  }
  .brand-name {
    font-weight: 700; font-size: 38px; line-height: 1;
    color: var(--brand-green); letter-spacing: -0.5px;
    white-space: nowrap;
  }
  .brand-sub {
    font-weight: 400; font-size: 15px; line-height: 1.3; color: var(--brand-green);
    margin-top: 2px; white-space: nowrap;
  }
  .divider {
    position: absolute; left: 345px; top: 44px;
    width: 1px; height: 100px; background: var(--divider-grey);
  }
  .contacts {
    position: absolute; left: 358px; top: 52px;
    list-style: none;
  }
  .contacts li {
    display: flex; align-items: center; gap: 7px;
    font-size: 12px; color: var(--text-grey);
    height: 24px; white-space: nowrap;
  }
  .contacts svg { width: 13px; height: 13px; flex: none; }
  .address {
    position: absolute; right: 215px; top: 158px;
    text-align: right; font-size: 12.5px; line-height: 1.6;
    color: var(--text-grey); font-style: normal; white-space: nowrap;
  }
  .rule-green {
    position: absolute; left: 0; right: 0; top: 238px;
    height: 2px; background: var(--brand-green);
  }
  .name-band {
    position: absolute; left: 0; right: 0; top: 243px; height: 46px;
    background: var(--brand-blue);
    display: flex; align-items: center; justify-content: center; gap: 6px;
    color: #fff; white-space: nowrap;
  }
  .person-name { font-weight: 700; font-size: 17px; }
  .person-title { font-weight: 300; font-size: 13px; }

  /* Back */
  .card-back { background: var(--brand-green); }
  .back-brand {
    position: absolute; left: 0; right: 0; top: 100px;
    display: flex; align-items: center; justify-content: center; gap: 10px;
    color: #fff;
  }
  .back-brand .brand-mark { background: #fff; width: 20px; height: 20px; }
  .back-brand .brand-name { color: #fff; font-size: 44px; }
  .back-url {
    position: absolute; right: 60px; bottom: 48px;
    color: #fff; font-size: 14px; letter-spacing: 3px; font-weight: 400;
  }
</style>
</head>
<body>
<main class="sheet">
  <section class="card card-front">
    <div class="brand">
      <div class="brand-row">
        <span class="brand-mark"></span>
        <span class="brand-name">NovaLube</span>
      </div>
      <span class="brand-sub">Oil Services</span>
    </div>

    <div class="divider"></div>

    <ul class="contacts">
      <li>
        <svg viewBox="0 0 14 14"><circle cx="7" cy="7" r="7" fill="var(--icon-orange)"/><path d="M4.5 3.8c.4-.4.9-.3 1.1.1l.6 1.2c.2.3.1.6-.2.8l-.4.3c.4.9 1.1 1.6 2 2l.3-.4c.2-.3.5-.4.8-.2l1.2.6c.4.2.5.7.1 1.1-.6.7-1.5.8-2.4.3C6 8.9 5 7.9 4.3 6.5c-.5-.9-.4-1.9.2-2.7z" fill="#fff"/></svg>
        +61 400 318 275
      </li>
      <li>
        <svg viewBox="0 0 14 14"><circle cx="7" cy="7" r="7" fill="var(--icon-orange)"/><rect x="3.5" y="4.5" width="7" height="5" fill="#fff"/><path d="M3.5 4.5 7 7.3l3.5-2.8" fill="none" stroke="var(--icon-orange)" stroke-width="0.9"/></svg>
        daniel@novalube.co.nz
      </li>
      <li>
        <svg viewBox="0 0 14 14"><circle cx="7" cy="7" r="7" fill="var(--icon-orange)"/><circle cx="7" cy="7" r="3.6" fill="none" stroke="#fff" stroke-width="0.9"/><path d="M3.4 7h7.2M7 3.4c-1.6 2-1.6 5.2 0 7.2M7 3.4c1.6 2 1.6 5.2 0 7.2" fill="none" stroke="#fff" stroke-width="0.8"/></svg>
        www.novalube.com.au
      </li>
    </ul>

    <address class="address">
      NovaLube Oil Services 412 Harbour Road<br>
      PO Box 5310 | Eastbrook<br>
      Queensland 4170
    </address>

    <div class="rule-green"></div>
    <div class="name-band">
      <span class="person-name">Daniel Hartley NZCE (Mech) P&amp;P,</span>
      <span class="person-title">Director</span>
    </div>
  </section>

  <section class="card card-back">
    <div class="back-brand">
      <span class="brand-mark"></span>
      <span class="brand-name">NovaLube</span>
    </div>
    <span class="back-url">www.novalube.com.au</span>
  </section>
</main>
</body>
</html>
```